BOLD & MINIMALIST DESIGN NEEDED

We want a very bold but minimalistic business card design that is impactful and utilizes both sides of the business card. Our current logo is included for your use.

We want bold fonts and good use of negative space. We don't want the logo to overpower the design.

Target Market(s)

Professionals who are building new commercial buildings.

Industry/Entity Type

Construction

Contact Information for Business Card

Name, Title, email, office phone, cell phone, website

Font styles to use
Serif
Sans Serif

Requirements
Must have
• Bold design!

```html
<!DOCTYPE html>
<html lang="en">
<head>
<meta charset="utf-8">
<title>Ridgeline — Business Card</title>
<link href="https://fonts.googleapis.com/css2?family=Arimo:wght@400;700&display=swap" rel="stylesheet">
<style>
  :root{
    --canvas:#e4e4e4;
    --white:#ffffff;
    --ink:#0b0b0c;
    --green:#86c42c;
    --green-light:#b4de7a;
  }
  *{box-sizing:border-box;margin:0;padding:0}
  html,body{width:1200px;height:1200px;overflow:hidden}
  body{background:var(--canvas);font-family:"Arimo",Arial,sans-serif;position:relative}

  .card{position:absolute;left:255px;width:690px;height:394px;overflow:hidden}
  .card--front{top:170px;display:flex;background:var(--ink)}
  .card--back{top:640px;background:radial-gradient(ellipse at 50% 45%,var(--green-light) 0%,var(--green) 62%);display:flex;align-items:center;justify-content:center}

  .front__brand{width:381px;background:var(--white);display:flex;align-items:center;justify-content:center}
  .front__divider{width:9px;background:var(--green)}
  .front__info{flex:1;padding:112px 0 0 46px;color:var(--white)}

  .brand-name{display:flex;align-items:center;gap:10px;font-weight:700;color:var(--ink);font-size:34px;letter-spacing:1px;white-space:nowrap}
  .brand-name__mark{width:18px;height:18px;background:var(--green);flex:none}

  .person__name{color:var(--green);font-weight:700;font-size:26px;line-height:1}
  .person__title{font-size:16px;margin-top:6px}

  .contacts{list-style:none;margin-top:40px}
  .contacts li{display:flex;align-items:center;gap:12px;font-size:16px;line-height:20.5px;white-space:nowrap}
  .contacts svg{width:14px;height:14px;flex:none}

  .back__brand{font-size:56px;letter-spacing:2px;gap:18px}
  .back__brand .brand-name__mark{width:30px;height:30px;background:var(--ink)}
</style>
</head>
<body>
  <section class="card card--front" aria-label="Business card front">
    <div class="front__brand">
      <div class="brand-name"><span class="brand-name__mark"></span>RIDGELINE</div>
    </div>
    <div class="front__divider"></div>
    <div class="front__info">
      <h1 class="person__name">DANIEL REYES</h1>
      <p class="person__title">President</p>
      <ul class="contacts">
        <li><svg viewBox="0 0 24 24" aria-hidden="true"><path fill="#86c42c" d="M6.6 10.8a15 15 0 0 0 6.6 6.6l2.2-2.2a1 1 0 0 1 1-.25 11.4 11.4 0 0 0 3.6.57 1 1 0 0 1 1 1V20a1 1 0 0 1-1 1A17 17 0 0 1 3 4a1 1 0 0 1 1-1h3.5a1 1 0 0 1 1 1c0 1.25.2 2.45.57 3.57a1 1 0 0 1-.25 1z"/></svg>555-210-4870</li>
        <li><svg viewBox="0 0 24 24" aria-hidden="true"><rect x="6" y="1.5" width="12" height="21" rx="2" fill="none" stroke="#86c42c" stroke-width="2.5"/><circle cx="12" cy="19" r="1.3" fill="#86c42c"/></svg>555-318-9462</li>
        <li><svg viewBox="0 0 24 24" aria-hidden="true"><rect x="2" y="5" width="20" height="14" fill="#86c42c"/><path d="M2 5l10 8 10-8" fill="none" stroke="#0b0b0c" stroke-width="2"/></svg>info@ridgelinebuild.com</li>
        <li><svg viewBox="0 0 24 24" aria-hidden="true"><circle cx="12" cy="12" r="10" fill="#86c42c"/><path d="M7 7c2 1 3 3 2 5s1 3 0 5M14 4c0 3 3 3 4 5s-2 3-1 6" fill="none" stroke="#0b0b0c" stroke-width="1.6"/></svg>www.ridgelinebuild.com</li>
      </ul>
    </div>
  </section>

  <section class="card card--back" aria-label="Business card back">
    <div class="brand-name back__brand"><span class="brand-name__mark"></span>RIDGELINE</div>
  </section>
</body>
</html>
```